website update

We need to redesign our current website to be more personalised and sophisticated. We are physiotherapy clinic based in sydney australia, offer a range of clinical service such as Physiotherapy, Massage, sports injuries rehabilitation, Women's health (incontinency etc), Pilates classes, back pain exercise program, acupuncture, Gait analysis.
our current website is www.brightlanehealth.com.au
an example of ideal website is http://quillbrookrehabstudio.com/
homepage: with a revolving displaying attached photos which is linked to relevants page

```html
<!DOCTYPE html>
<html lang="en">
<head>
<meta charset="utf-8">
<title>Brightlane Health – Physiotherapy &amp; Sports Clinic</title>
<link href="https://fonts.googleapis.com/css2?family=Roboto:wght@400;500&display=swap" rel="stylesheet">
<style>
:root{
  --green:#2e9b57;
  --green-dark:#23854a;
  --lime:#9cc43a;
  --lime-dark:#7fa42a;
  --ink:#1f1f1f;
  --text:#555;
  --band:#232323;
  --mint:#d9efe3;
  --white:#fff;
}
*{margin:0;padding:0;box-sizing:border-box}
html,body{width:934px;height:1200px;overflow:hidden}
body{position:relative;background:var(--white);font-family:'Roboto',sans-serif;color:var(--text)}
.abs{position:absolute}
.top-rule{left:0;top:0;width:934px;height:6px;background:var(--green)}
.brand{left:136px;top:30px;display:flex;align-items:center;gap:10px}
.brand-mark{width:44px;height:44px;border-radius:50%;background:var(--green)}
.brand-name{font-size:22px;font-weight:500;color:var(--green);line-height:1.1}
.brand-name small{display:block;font-size:9px;font-weight:500;color:var(--green);letter-spacing:.3px}
.contact{right:132px;top:34px;text-align:right;font-size:9.5px;color:var(--ink);line-height:21px}
.contact svg{vertical-align:-2px;margin-right:4px}
.stage{left:0;top:97px;width:934px;height:381px;background:var(--band)}
.nav{left:135px;top:97px;width:667px;height:50px;background:linear-gradient(var(--green),var(--green-dark));display:flex}
.nav a{color:var(--white);text-decoration:none;font-size:10.5px;line-height:50px;padding:0 10.5px;border-right:1px solid rgba(255,255,255,.15)}
.nav a.current{background:var(--lime);padding:0 19px}
.nav a:last-child{border:0}
.hero{left:135px;top:147px;width:667px;height:331px;background:linear-gradient(120deg,#3a3a3a,#cfcfcf 55%,#e9e9e9)}
.caption{left:135px;top:423px;width:667px;height:55px;background:rgba(40,40,40,.6);color:var(--white);font-size:14.5px;line-height:55px;padding-left:29px}
.dot{width:10px;height:10px;border-radius:50%;background:var(--white);top:445px}
.dot.on{background:var(--green)}
.feature{top:478px;height:248px;background:radial-gradient(ellipse at 50% 35%,#fff 20%,var(--mint) 100%);text-align:center;box-shadow:0 10px 10px -8px rgba(0,0,0,.35)}
.feature h3{font-weight:400;font-size:13px;color:var(--ink);margin-top:26px;letter-spacing:.2px}
.feature .ring{width:72px;height:72px;border:1px solid var(--green);border-radius:50%;margin:14px auto 0;display:flex;align-items:center;justify-content:center}
.feature .ring span{width:28px;height:28px;border-radius:50%;background:var(--ink)}
.feature p{font-size:10px;line-height:16px;margin:14px 20px 0;text-align:justify}
.btn{display:inline-block;background:var(--lime);color:var(--white);font-size:10px;border-bottom:3px solid var(--lime-dark);border-radius:2px}
.feature .btn{width:75px;line-height:22px;margin-top:18px}
.welcome-img{left:136px;top:778px;width:192px;height:120px;border:3px solid #eee;box-shadow:0 0 3px rgba(0,0,0,.4);background:linear-gradient(90deg,#666,#c9c9c9 50%,#eee)}
.welcome{left:346px;top:778px;width:446px}
.welcome h2{font-weight:400;font-size:13.5px;color:var(--green)}
.welcome p{font-size:9px;line-height:16px;margin-top:6px;color:#444;letter-spacing:.2px}
.welcome .btn{margin-top:10px;padding:0 12px;line-height:23px}
.section-title{font-weight:400;font-size:14px;color:var(--green)}
.news{left:138px;width:170px}
.date{width:38px;height:41px;border:1px solid #ddd;background:#f3f3f3;text-align:center;float:left}
.date b{display:block;background:var(--white);font-size:12px;font-weight:500;color:var(--ink);line-height:27px}
.date i{font-style:normal;font-size:7px;line-height:13px}
.news h4{font-weight:400;font-size:9px;color:var(--green);margin-left:43px;padding-top:3px}
.news p{font-size:8px;color:var(--ink);margin-left:43px;margin-top:8px}
.rule{left:140px;top:1025px;width:164px;border-top:1px dotted #777}
.card{top:966px;width:148px;height:120px;background:var(--white);box-shadow:0 2px 4px rgba(0,0,0,.3);text-align:center}
.card .pic{height:84px}
.card span{display:block;font-size:9px;color:var(--green);line-height:36px}
.footer{left:0;top:1116px;width:934px;height:78px;background:var(--green)}
.footer-base{left:0;top:1194px;width:934px;height:6px;background:var(--ink)}
.footer-links{left:137px;top:1140px;font-size:8.5px;color:var(--white)}
.footer-links a{color:var(--white);text-decoration:none}
.copy{left:137px;top:1160px;font-size:8.5px;color:var(--white)}
.social{top:1146px;width:23px;height:23px;border-radius:50%;border:2px solid #e8e8e8}
</style>
</head>
<body>
<div class="abs top-rule"></div>

<div class="abs brand">
  <span class="brand-mark"></span>
  <div class="brand-name">Brightlane Health<small>PHYSIOTHERAPY &amp; SPORTS CLINIC</small></div>
</div>
<div class="abs contact">
  <div><svg width="10" height="8" viewBox="0 0 10 8"><rect width="10" height="8" fill="#2e9b57"/><path d="M0 0l5 4 5-4" stroke="#fff" fill="none"/></svg>info@brightlanehealth.com.au</div>
  <div><svg width="8" height="11" viewBox="0 0 8 11"><path d="M4 11C1 7 0 5.5 0 4a4 4 0 018 0c0 1.5-1 3-4 7z" fill="#2e9b57"/><circle cx="4" cy="4" r="1.6" fill="#fff"/></svg>Suite 4, Harbour Arcade, 212 Elm Street, Westvale 2071</div>
</div>

<div class="abs stage"></div>
<nav class="abs nav">
  <a class="current">Home</a><a>About us</a><a>Common conditions</a><a>Treatments</a><a>Specialised services</a><a>OH&amp;S / Workplace Assessment</a><a>Contact Us</a>
</nav>
<div class="abs hero" role="img" aria-label="Physiotherapist treating a patient lying on a treatment table"></div>
<div class="abs caption">Lorem Ipsum is simply dummy text of the printing and typesetting industry.</div>
<span class="abs dot" style="left:705px"></span>
<span class="abs dot on" style="left:723px"></span>
<span class="abs dot" style="left:743px"></span>
<span class="abs dot" style="left:764px"></span>

<section class="abs feature" style="left:135px;width:223px">
  <h3>WE TREAT</h3>
  <div class="ring"><span role="img" aria-label="Lunging athlete icon"></span></div>
  <p>Lorem Ipsum is simply dummy text of the printing and typesetting industry. Lorem Ipsum has been t1500s, when an</p>
  <span class="btn">Read More</span>
</section>
<section class="abs feature" style="left:359px;width:223px">
  <h3>WE OFFER</h3>
  <div class="ring"><span role="img" aria-label="Massage treatment icon"></span></div>
  <p>Lorem Ipsum is simply dummy text of the printing and typesetting industry. Lorem Ipsum has been t1500s, when an</p>
  <span class="btn">Read More</span>
</section>
<section class="abs feature" style="left:584px;width:218px">
  <h3>SPECIALISED SERVICES</h3>
  <div class="ring"><span role="img" aria-label="Head and neck profile icon"></span></div>
  <p>Lorem Ipsum is simply dummy text of the printing and typesetting industry. Lorem Ipsum has been t1500s, when an</p>
  <span class="btn">Read More</span>
</section>

<div class="abs welcome-img" role="img" aria-label="Spine model with a treatment instrument"></div>
<section class="abs welcome">
  <h2>WELCOME TO BRIGHTLANE SPINAL &amp; SPORTS PHYSIOTHERAPY CLINIC</h2>
  <p>Lorem Ipsum is simply dummy text of the printing and typesetting industry. Lorem Ipsum has been the industry's standard dummy text ever since the 1500s, when an unknown printer took a galley of type and scrambled it to make a type specimen book. It has survived not only five centuries, but also the leap into electronic typesetting, remaining essentially unchanged.</p>
  <span class="btn">READ MORE</span>
</section>

<h2 class="abs section-title" style="left:142px;top:940px">LATEST NEWS</h2>
<h2 class="abs section-title" style="left:338px;top:940px">CLINICAL SERVICE</h2>
<svg class="abs" style="left:783px;top:940px" width="20" height="14" viewBox="0 0 20 14"><path d="M7 1L2 7l5 6M13 1l5 6-5 6" stroke="#222" stroke-width="1.6" fill="none"/></svg>

<div class="abs news" style="top:973px">
  <div class="date"><b>20</b><i>mar</i></div>
  <h4>NEWS HEADLINE HERE</h4>
  <p>Lorem ipsum dolor sit amet, consec-</p>
</div>
<div class="abs rule"></div>
<div class="abs news" style="top:1036px">
  <div class="date"><b>20</b><i>mar</i></div>
  <h4>NEWS HEADLINE HERE</h4>
  <p>Lorem ipsum dolor sit amet, consec-</p>
</div>

<div class="abs card" style="left:338px"><div class="pic" role="img" aria-label="Physiotherapist treating a patient's leg" style="background:linear-gradient(135deg,#2b3440,#d8dde2)"></div><span>PHYSIOTHERAPY</span></div>
<div class="abs card" style="left:496px"><div class="pic" role="img" aria-label="Therapist massaging a client's arm" style="background:linear-gradient(135deg,#e9e2da,#a88b77 60%,#394047)"></div><span>MASSAGE</span></div>
<div class="abs card" style="left:656px"><div class="pic" role="img" aria-label="Acupuncture needles held in fingers" style="background:linear-gradient(90deg,#d8a890,#2a2a2a 55%,#444)"></div><span>SPORTS INJURIES</span></div>

<footer class="abs footer"></footer>
<div class="abs footer-base"></div>
<div class="abs footer-links"><a>Home</a> | <a>Blog</a> | <a>About us</a> | <a>FAQ</a> | <a>Contact Us</a> | <a>Privacy Policy</a></div>
<div class="abs copy">Copyrights © 2014 . All Right Reserved.</div>
<span class="abs social" style="left:694px;background:#3b5a9a"></span>
<span class="abs social" style="left:722px;background:#d2473a"></span>
<span class="abs social" style="left:750px;background:#2aa3e0"></span>
<span class="abs social" style="left:778px;background:#f0731d"></span>
</body>
</html>
```